Business Card Design - Amberfield Court

We are looking at a new design for our business cards that has a modern and professional look. We run a residential aged care facility focussing on the care of residents. The cards will be used for potential clients, consultants and business opportunities in this sector. Blue and white is our main colours and would to see these colours incorporated in the design.
Industry/Entity Type
Business
Contact Information for Business Card
Amberfield Court, Darren Walsh, dwalsh@amberfieldcourt.com.au, Finance Manager, 0472 639 208, BCom, 37 Marrabel Crescent, Brindle Vale, Qld 4093.
Look and feel
Each slider illustrates characteristics of the customer's brand and the style your logo design should communicate.

```html
<!DOCTYPE html>
<html lang="en">
<head>
<meta charset="utf-8">
<title>Amberfield Court – Business Card</title>
<link rel="stylesheet" href="https://fonts.googleapis.com/css2?family=Encode+Sans+Condensed:wght@300;400;600&display=swap">
<style>
  :root {
    --page: #ecebe8;
    --card: #ffffff;
    --band: #aaa29b;
    --blue: #4f7d9a;
    --ink-light: #ffffff;
    --shadow: rgba(40, 35, 30, 0.18);
  }
  * { box-sizing: border-box; margin: 0; padding: 0; }
  html, body {
    width: 1200px;
    height: 950px;
    overflow: hidden;
    background: var(--page);
    font-family: "Encode Sans Condensed", "Arial Narrow", sans-serif;
  }
  .canvas {
    position: relative;
    width: 1200px;
    height: 950px;
  }
  .card {
    position: absolute;
    width: 700px;
    height: 400px;
    background: var(--card);
    border-radius: 26px;
    overflow: hidden;
    box-shadow: 0 10px 28px var(--shadow);
  }

  /* Front */
  .card--front { left: 80px; top: 50px; }
  .front-brand {
    position: absolute;
    left: 60px;
    top: 110px;
    display: flex;
    align-items: center;
    gap: 14px;
    color: var(--blue);
    font-size: 30px;
    font-weight: 400;
    letter-spacing: 1.5px;
    text-transform: uppercase;
    line-height: 1;
  }
  .brand-dot {
    width: 22px;
    height: 22px;
    border-radius: 50%;
    background: var(--blue);
    flex: none;
  }
  .front-band {
    position: absolute;
    left: 0;
    right: 0;
    top: 190px;
    height: 170px;
    background: var(--band);
    color: var(--ink-light);
    padding: 22px 0 0 330px;
  }
  .person-name {
    font-size: 26px;
    font-weight: 600;
    letter-spacing: 0.3px;
    line-height: 1.1;
  }
  .person-role {
    font-size: 17px;
    font-weight: 300;
    margin-bottom: 14px;
  }
  .contact-line {
    font-size: 16px;
    font-weight: 300;
    line-height: 1.45;
    white-space: nowrap;
  }

  /* Back */
  .card--back { left: 420px; top: 500px; }
  .back-brand {
    position: absolute;
    inset: 0;
    display: flex;
    align-items: center;
    justify-content: center;
    gap: 18px;
    color: var(--blue);
    font-size: 44px;
    font-weight: 400;
    letter-spacing: 3px;
    text-transform: uppercase;
    line-height: 1;
    white-space: nowrap;
  }
  .back-brand .brand-dot { width: 30px; height: 30px; }
</style>
</head>
<body>
<main class="canvas">

  <section class="card card--front" aria-label="Business card front">
    <div class="front-brand">
      <span class="brand-dot" aria-hidden="true"></span>
      <span class="brand-name">Amberfield Court</span>
    </div>
    <div class="front-band">
      <p class="person-name">Darren Walsh BCom</p>
      <p class="person-role">Finance Manager</p>
      <p class="contact-line">37 Marrabel Crescent, Brindle Vale, Qld 4093</p>
      <p class="contact-line">0472 639 208 | dwalsh@amberfieldcourt.com.au</p>
      <p class="contact-line">www.amberfieldcourt.com.au</p>
    </div>
  </section>

  <section class="card card--back" aria-label="Business card back">
    <div class="back-brand">
      <span class="brand-dot" aria-hidden="true"></span>
      <span class="brand-name">Amberfield Court</span>
    </div>
  </section>

</main>
</body>
</html>
```